Corporate Business Card

Very professional, Modern, Not to busy, include phone address email, website
(253) 617-4930, 18761 52nd Avenue S, Kent, WA 98047, martin@plumlinegroup.com, varkoworks.com

Target Market(s)

Manufacturing

Industry/Entity Type

Aero, machining, manufacturing, Off road racing

Contact Information for Business Card

Phone, address email, website

```html
<!DOCTYPE html>
<html lang="en">
<head>
<meta charset="utf-8">
<title>Varko Works – Business Card</title>
<link href="https://fonts.googleapis.com/css2?family=Montserrat:wght@400;500;700&display=swap" rel="stylesheet">
<style>
  :root {
    --navy: #15366f;
    --red: #d3232a;
    --white: #ffffff;
    --ink: #1b1b1b;
    --backdrop: #d6d6d6;
  }
  * { box-sizing: border-box; margin: 0; padding: 0; }
  html, body { width: 1200px; height: 813px; overflow: hidden; }
  body {
    background: var(--backdrop);
    font-family: "Montserrat", sans-serif;
    display: flex;
    align-items: center;
    justify-content: center;
    gap: 40px;
  }
  .card {
    position: relative;
    width: 540px;
    height: 310px;
    border-radius: 18px;
    overflow: hidden;
  }
  .card-front { background: var(--white); }
  .card-back { background: var(--navy); }

  .card-stripes { position: absolute; inset: 0; width: 100%; height: 100%; }

  .brand {
    position: absolute;
    font-weight: 700;
    letter-spacing: 0.02em;
    white-space: nowrap;
  }
  .brand-front {
    top: 58px;
    right: 60px;
    font-size: 38px;
    color: var(--navy);
  }
  .brand-rule-front {
    position: absolute;
    top: 112px;
    right: 200px;
    width: 150px;
    height: 2px;
    background: var(--navy);
  }

  .address {
    position: absolute;
    left: 34px;
    top: 150px;
    font-size: 13px;
    line-height: 1.35;
    color: var(--ink);
  }
  .contact-list {
    position: absolute;
    left: 34px;
    top: 206px;
    list-style: none;
    font-size: 13px;
    color: var(--ink);
  }
  .contact-item {
    display: flex;
    align-items: center;
    gap: 8px;
    line-height: 1.55;
  }
  .contact-icon { width: 12px; height: 12px; flex: none; }

  .band-website {
    position: absolute;
    right: 22px;
    bottom: 11px;
    font-size: 11px;
    color: var(--white);
    letter-spacing: 0.02em;
  }

  .brand-back {
    top: 112px;
    left: 0;
    right: 0;
    text-align: center;
    font-size: 52px;
    color: var(--white);
  }
  .brand-rule-back {
    position: absolute;
    top: 188px;
    left: 150px;
    width: 240px;
    height: 2px;
    background: var(--white);
  }
</style>
</head>
<body>

  <section class="card card-front" aria-label="Business card front">
    <svg class="card-stripes" viewBox="0 0 540 310" aria-hidden="true">
      <polygon points="255,310 280,310 330,250 305,250" fill="var(--navy)"/>
      <polygon points="283,310 320,310 370,250 333,250" fill="var(--red)"/>
      <polygon points="323,310 540,310 540,250 373,250" fill="var(--navy)"/>
    </svg>

    <div class="brand brand-front">Varko Works</div>
    <div class="brand-rule-front"></div>

    <p class="address">18761 52nd Avenue S<br>Kent, WA 98047</p>

    <ul class="contact-list">
      <li class="contact-item">
        <svg class="contact-icon" viewBox="0 0 12 12" aria-hidden="true">
          <path d="M2.5 1 L4.5 1 L5.2 3.5 L4 4.4 C4.6 5.8 6 7.2 7.6 8 L8.5 6.8 L11 7.5 L11 9.5 C11 10.3 10.3 11 9.5 11 C5 11 1 7 1 2.5 C1 1.7 1.7 1 2.5 1 Z" fill="var(--red)"/>
        </svg>
        (253) 617-4930
      </li>
      <li class="contact-item">
        <svg class="contact-icon" viewBox="0 0 12 12" aria-hidden="true">
          <rect x="0.5" y="2" width="11" height="8" fill="var(--red)"/>
          <path d="M0.5 2 L6 6.5 L11.5 2" stroke="var(--white)" stroke-width="1" fill="none"/>
        </svg>
        martin@plumlinegroup.com
      </li>
      <li class="contact-item">
        <svg class="contact-icon" viewBox="0 0 12 12" aria-hidden="true">
          <circle cx="6" cy="6" r="5.5" fill="var(--red)"/>
          <ellipse cx="6" cy="6" rx="2.4" ry="5.5" stroke="var(--white)" stroke-width="0.8" fill="none"/>
          <line x1="0.5" y1="6" x2="11.5" y2="6" stroke="var(--white)" stroke-width="0.8"/>
        </svg>
        www.varkoworks.com
      </li>
    </ul>

    <span class="band-website">www.varkoworks.com</span>
  </section>

  <section class="card card-back" aria-label="Business card back">
    <div class="brand brand-back">Varko Works</div>
    <div class="brand-rule-back"></div>
  </section>

</body>
</html>
```